Structural Engineering Business Card

Brookvane Drafting does residential house plans for clients in Central Florida. Would like simple but elegant business card that is appropriate for a house plan engineering company. Prefer black business card with black/white them but open to other shades of blue. I uploaded a sample card that I came across that looked good but please come up with your own creative designs.

Contact Information for Business Card

Name, Title, Phone, Email, Address, website

```html
<!DOCTYPE html>
<html lang="en">
<head>
<meta charset="utf-8">
<title>Brookvane Drafting – Business Card</title>
<link rel="stylesheet" href="https://fonts.googleapis.com/css2?family=Arimo:wght@400;700&display=swap">
<style>
  :root {
    --backdrop: #262626;
    --card: #1c1c1c;
    --decor: #343434;
    --ink: #ffffff;
    --ink-soft: #f2f2f2;
  }
  * { margin: 0; padding: 0; box-sizing: border-box; }
  html, body { width: 1200px; height: 1059px; overflow: hidden; }
  body {
    background: var(--backdrop);
    position: relative;
    font-family: "Arimo", Arial, sans-serif;
    color: var(--ink);
  }
  .card {
    position: absolute;
    background: var(--card);
    border-radius: 18px;
    box-shadow: 0 14px 26px rgba(0,0,0,0.55);
    overflow: hidden;
  }
  .card--front { left: 257px; top: 89px; width: 687px; height: 390px; }
  .card--back  { left: 254px; top: 547px; width: 693px; height: 393px; }

  .decor-region {
    position: absolute;
    left: 262px; top: 21px;
    width: 405px; height: 346px;
    border-radius: 24px;
    background: linear-gradient(160deg, #383838, var(--decor));
  }

  .brand {
    position: absolute;
    display: flex;
    align-items: center;
    font-weight: 700;
    color: var(--ink);
    white-space: nowrap;
    letter-spacing: 0.5px;
  }
  .brand__mark { background: var(--ink); flex: none; }
  .card--front .brand { left: 35px; top: 44px; font-size: 30px; line-height: 1.08; gap: 10px; }
  .card--front .brand__mark { width: 16px; height: 16px; align-self: flex-start; margin-top: 8px; }
  .card--back .brand {
    left: 0; right: 0; top: 170px;
    justify-content: center;
    font-size: 42px; gap: 16px;
  }
  .card--back .brand__mark { width: 26px; height: 26px; }

  .contact { position: absolute; left: 35px; top: 140px; }
  .contact__name { font-size: 24px; font-weight: 700; letter-spacing: 0.6px; line-height: 1; }
  .contact__title { font-size: 17px; margin-top: 6px; color: var(--ink-soft); }
  .contact__address { font-size: 17px; line-height: 25px; margin-top: 18px; color: var(--ink-soft); }
  .contact__list { list-style: none; margin-top: 14px; }
  .contact__list li {
    display: flex; align-items: center; gap: 6px;
    font-size: 17px; height: 28.5px; color: var(--ink-soft);
  }
  .contact__list svg { width: 13px; height: 13px; fill: var(--ink); flex: none; }
</style>
</head>
<body>

<section class="card card--front" aria-label="Business card front">
  <div class="decor-region" role="img" aria-label="Large faint map of Florida as background decoration"></div>

  <div class="brand"><span class="brand__mark"></span><span>BROOKVANE<br>DRAFTING</span></div>

  <div class="contact">
    <p class="contact__name">MARTIN ELLERY</p>
    <p class="contact__title">Founder/CEO</p>
    <p class="contact__address">2710 Cedar Row Ste 140<br>Lakewood, FL 32801</p>
    <ul class="contact__list">
      <li>
        <svg viewBox="0 0 16 16" aria-hidden="true"><path d="M1 5c0-2 3-3 7-3s7 1 7 3v1h-4V5H5v1H1z M3 7h10l1 7H2z M6 9h4v3H6z"/></svg>
        407.555.0182
      </li>
      <li>
        <svg viewBox="0 0 16 16" aria-hidden="true"><path d="M1 3h14v2L8 9 1 5z M1 6.5l7 4 7-4V13H1z"/></svg>
        info@brookvane.com
      </li>
      <li>
        <svg viewBox="0 0 16 16" aria-hidden="true"><path d="M8 0a8 8 0 1 0 0 16A8 8 0 0 0 8 0zm0 1.6a6.4 6.4 0 1 1 0 12.8A6.4 6.4 0 0 1 8 1.6zM5 4l3 1 1 3-2 1 1 3-3-2-1-3z"/></svg>
        www.brookvane.com
      </li>
    </ul>
  </div>
</section>

<section class="card card--back" aria-label="Business card back">
  <div class="brand"><span class="brand__mark"></span>BROOKVANE DRAFTING</div>
</section>

</body>
</html>
```